Pull Up Banner - Recruitment Company

We would like a design for a pull up banner.

For context: we are a recruitment business. We specialise in helping people in healthcare industry to find jobs in Australia.

I have come up with several ideas and text for the banner. Feel free to use the following as you see appropriate:

- Our logo (see attached)
- 'Healthcare Recruitment Agency'
- Some sort of imagine / cartoon of medical professionals (ie. doctor, nurse, physiotherapist, speech pathologist). A cartoon is more friendly than committing to a photo
- 'Empowering your next career move'
- 'Discover tailored opportunities based on your career preferences'
- Dot points (allied health, nursing, medical imaging)
- Contact info at the bottom including our website (www.quellastaffing.com.au, our Instagram handle @quellastaffing, Mobile: XXXX XXX XXX. The title section for contact information could be 'Get in touch:'

Feel free to submit a couple of designs and we can merge aspects that look good on your designs and find the perfect fit.
Thank you
Updates

Hello,

Thank you for your initial submissions to this project. I appreciate the time you've invested.

After reviewing the first attempt, I'd like to share some feedback and initial observations:

- Professionalism and engagement: Is the overall appearance of the banner professional? It's crucial that we have a high-quality design as this will represent our business.

- Image selection: The image (whether cartoon or real people) appears quite generic. Please consider submitting the banner with a few different photos in the middle for us to choose from. Ensure the image is a good fit and not simply a generic stock photo.

- Contact section: Kindly remove the phone number; we no longer wish to include it on the banner. Instead, please include our website (www.quellastaffing.com.au) and Instagram handle (@quellastaffing).

- Color scheme: White, black, and red/pink are preferred, or alternatively, blue. However, please avoid incorporating too many different colors as it may detract from the professional appearance.

We will be printing the design on a banner and require it to look professional and engaging.

Thank you once again for your submissions. I hope the feedback provided above is helpful.

Warm regards,

Target Market(s)

Allied Health Australia

Font styles to use
Serif

Colors
0054AA
0677BA
7BADD7
CADEEF
E8F1F8
0094D4
00A9DD
6FCCEA
C7EBF8
E9F6FB
EB3D1F
EC4F4E
F09395
F8D3D4
FCEDEE

```html
<!DOCTYPE html>
<html lang="en">
<head>
<meta charset="utf-8">
<title>Quella Staffing – Pull Up Banner</title>
<link href="https://fonts.googleapis.com/css2?family=Lexend:wght@400;700;800&family=Poppins:wght@500;600&family=Montserrat:wght@700;800&display=swap" rel="stylesheet">
<style>
  :root {
    --stage: #dedede;
    --navy: #0b168a;
    --navy-deep: #0b1155;
    --royal: #3343d8;
    --sky: #8bb8ff;
    --white: #ffffff;
    --ink: #2a2a2a;
    --lilac: #b88ad8;
  }
  * { margin: 0; padding: 0; box-sizing: border-box; }
  html, body {
    width: 1200px; height: 2400px; overflow: hidden;
    background: var(--stage);
  }
  .banner-frame {
    position: absolute; left: 87px; top: 18px;
    width: 1026px; height: 2363px;
  }
  .banner {
    position: absolute; left: 0; top: 0;
    width: 987px; height: 2272px;
    transform: scale(1.04); transform-origin: 0 0;
    overflow: hidden; background: var(--white);
  }
  .backdrop { position: absolute; inset: 0; }
  .line { position: absolute; left: 0; width: 100%; text-align: center; line-height: 1; white-space: nowrap; }

  .brand-name {
    top: 88px; font-family: 'Lexend', sans-serif; font-weight: 700;
    color: var(--white); font-size: 118px; letter-spacing: 0.04em;
  }
  .brand-sub {
    top: 218px; font-family: 'Lexend', sans-serif; font-weight: 700;
    color: var(--white); font-size: 34px; letter-spacing: 0.32em;
  }
  .headline { font-family: 'Lexend', sans-serif; font-weight: 800; letter-spacing: -0.02em; }
  .headline--accent { top: 308px; font-size: 100px; color: var(--sky); }
  .headline--main { color: var(--white); font-size: 124px; }
  .headline--r { top: 388px; }
  .headline--a { top: 489px; }

  .scene-art {
    position: absolute; left: 95px; top: 705px; width: 800px; height: 755px;
    border-radius: 24px;
    background: linear-gradient(160deg, rgba(120,110,235,0.55), rgba(184,138,216,0.55));
  }

  .tagline { font-family: 'Lexend', sans-serif; color: var(--ink); }
  .tagline--light { top: 1540px; font-size: 80px; font-weight: 400; letter-spacing: -0.02em; }
  .tagline--bold { top: 1610px; font-size: 80px; font-weight: 800; letter-spacing: -0.02em; }
  .subline { top: 1710px; font-family: 'Poppins', sans-serif; font-weight: 500; font-size: 48px; color: var(--ink); letter-spacing: -0.01em; }

  .specialties { position: absolute; left: 0; top: 1818px; width: 100%; height: 140px; }
  .specialty {
    position: absolute; top: 0; width: 300px; margin-left: -150px; text-align: center;
  }
  .specialty__icon { display: block; margin: 10px auto 0; width: 66px; height: 64px; }
  .specialty__label {
    display: block; margin-top: 22px;
    font-family: 'Poppins', sans-serif; font-weight: 500; font-size: 33px; color: var(--ink);
  }
  .divider { position: absolute; top: 0; width: 2px; height: 140px; background: #e4e4e4; }

  .contact-title {
    top: 2005px; font-family: 'Montserrat', sans-serif; font-weight: 800;
    font-size: 45px; letter-spacing: 0.14em; color: var(--ink);
  }
  .contact-url {
    position: absolute; left: 95px; top: 2061px; width: 781px; height: 77px;
    border-radius: 39px; background: var(--navy);
    display: flex; align-items: center; justify-content: center;
    font-family: 'Montserrat', sans-serif; font-weight: 800; font-size: 40px;
    letter-spacing: 0.06em; color: var(--white);
  }
  .contact-handle {
    top: 2166px; font-family: 'Poppins', sans-serif; font-weight: 600;
    font-size: 32px; color: var(--navy);
  }
</style>
</head>
<body>
  <div class="banner-frame">
    <div class="banner">
      <svg class="backdrop" width="987" height="2272" viewBox="0 0 987 2272" aria-hidden="true">
        <rect width="987" height="2272" fill="var(--navy)"/>
        <polygon points="0,608 0,1033 475,818" fill="var(--navy-deep)"/>
        <polygon points="987,588 0,1033 0,1558 650,1250 987,1108" fill="var(--royal)"/>
        <polygon points="987,1108 987,1488 650,1250" fill="var(--navy-deep)"/>
        <polygon points="0,1558 650,1250 987,1488 987,2272 0,2272" fill="var(--white)"/>
      </svg>

      <div class="line brand-name">QUELLA</div>
      <div class="line brand-sub">STAFFING</div>

      <div class="line headline headline--accent">HEALTHCARE</div>
      <div class="line headline headline--main headline--r">RECRUITMENT</div>
      <div class="line headline headline--main headline--a">AGENCY</div>

      <div class="scene-art" role="img" aria-label="Illustration of a physiotherapist treating a patient's knee in a clinic room with an x-ray, wheelchair, exercise ball and plant"></div>

      <div class="line tagline tagline--light">EMPOWER YOUR</div>
      <div class="line tagline tagline--bold">NEXT CAREER MOVE</div>
      <div class="line subline">Tailored opportunities that fit you</div>

      <div class="specialties">
        <div class="specialty" style="left:203px">
          <svg class="specialty__icon" viewBox="0 0 66 64" role="img" aria-label="Allied health icon">
            <path d="M33 44 L15 26 A10 10 0 0 1 33 14 A10 10 0 0 1 51 26 Z" fill="var(--ink)"/>
            <path d="M6 50 H24 L34 56 L58 46" fill="none" stroke="var(--royal)" stroke-width="6" stroke-linecap="round"/>
          </svg>
          <span class="specialty__label">Allied Health</span>
        </div>
        <div class="divider" style="left:357px"></div>
        <div class="specialty" style="left:464px">
          <svg class="specialty__icon" viewBox="0 0 66 64" role="img" aria-label="Nursing icon">
            <rect x="14" y="36" width="38" height="26" rx="10" fill="var(--royal)"/>
            <circle cx="33" cy="20" r="13" fill="var(--ink)"/>
          </svg>
          <span class="specialty__label">Nursing</span>
        </div>
        <div class="divider" style="left:572px"></div>
        <div class="specialty" style="left:760px">
          <svg class="specialty__icon" viewBox="0 0 66 64" role="img" aria-label="Medical imaging icon">
            <circle cx="26" cy="26" r="18" fill="none" stroke="var(--royal)" stroke-width="8"/>
            <rect x="20" y="30" width="42" height="8" rx="3" fill="var(--ink)"/>
            <rect x="50" y="38" width="5" height="16" fill="var(--ink)"/>
          </svg>
          <span class="specialty__label">Medical Imaging</span>
        </div>
      </div>

      <div class="line contact-title">GET IN TOUCH</div>
      <div class="contact-url">www.quellastaffing.com.au</div>
      <div class="line contact-handle">@quellastaffing</div>
    </div>
  </div>
</body>
</html>
```